Lumra Learning Web Design Project

Who We are:
Lumra Learning is education information portal/ magazine, providing information about the Chinese and International education markets. Our aim is to help school principals improve there curriculum, and parents in understanding this curriculum.

Project Brief:
The site will include education news updates, educational services, curriculum developments and overseas study. We hope the site represents the cross cultural bridge between the west and east. The site will cover both the Sciences and Arts.

Note:
The logo design competition is also underway so we only need the website design

What We want:
This competition is for Design only no coding!
Design a home page based on Template 1,2 or 3. I only need to select one.
The design of an article page.

Optional
Design a Parvex Shutters metro style splash page.

Sites We like:
http://www.qv.com.cn/tonguebridge/default.aspx
http://www.dailyuniversitybulletin.co.uk/
http://kptz.sinocraftlearn.net/

Template Explanations:
Template 1-
The main information has a dynamic sliding category view that when clicked displays the relevant info.
In addition to the main upper menu it also has a left hand sliding menu that pops out on click or gesture

Template 2-
Has limited number of Articles most of the menus are drop downs from the top menu

Template 3-
No Top menu

Target Market(s)

Teachers, principals and parents

Industry/Entity Type

Education

Requirements
Should not have
• kindergarten preschool feel

```html
<!DOCTYPE html>
<html lang="fr">
<head>
<meta charset="utf-8">
<title>Lumra Learning</title>
<link href="https://fonts.googleapis.com/css2?family=Raleway:wght@400;500;600&family=Signika:wght@400;600;700&display=swap" rel="stylesheet">
<style>
:root{
  --page:#ececec;
  --white:#ffffff;
  --brand-red:#d9241c;
  --brand-blue:#1f5a8c;
  --nav-top:#4f86b8;
  --nav-bottom:#2b6198;
  --tag-blue:#3f78ab;
  --panel-grey:#f0f0f0;
  --footer:#333333;
  --footer-text:#cfcfcf;
  --footer-link:#bdbdbd;
  --icon-grey:#444444;
  --link-blue:#1f5a9c;
}
*{box-sizing:border-box;margin:0;padding:0}
html,body{width:965px;height:1200px;overflow:hidden}
body{background:var(--page);font-family:"Raleway",sans-serif;position:relative}
.abs{position:absolute}

.site-header{left:80px;top:10px;width:805px;height:82px;background:var(--white)}
.logo{left:16px;top:20px;display:flex;align-items:center;gap:8px}
.logo-dot{width:36px;height:36px;border-radius:50%;background:var(--brand-blue)}
.logo-name{font-family:"Signika",sans-serif;font-weight:600;font-size:17px;color:var(--brand-red);letter-spacing:.3px}
.search{left:497px;top:27px;width:254px;height:28px;border:1px solid #dcdcdc;border-radius:2px;background:#fff;font-size:9px;font-style:italic;color:#999;padding:8px 10px}
.search-btn{left:757px;top:27px;width:31px;height:27px;background:var(--brand-red);border-radius:3px;display:flex;align-items:center;justify-content:center}

.main-nav{left:81px;top:92px;width:804px;height:35px;display:flex;background:linear-gradient(var(--nav-top),var(--nav-bottom))}
.main-nav a{color:#fff;text-decoration:none;font-size:14px;display:flex;align-items:center;justify-content:center;border-right:1px solid #6f9cc7;height:100%}
.main-nav a.active{background:linear-gradient(#2c6aa6,#1c4f80)}

.side-menu{left:81px;top:137px;width:48px}
.side-menu .tile{width:48px;height:56px;background:var(--brand-red);margin-bottom:3px;display:flex;align-items:center;justify-content:center;border:1px solid #b71a14}
.social-rail{left:92px;top:634px;width:24px}
.social-rail span{display:block;width:14px;height:14px;border-radius:50%;background:var(--icon-grey);margin:0 auto 32px}

.content{left:137px;top:137px;width:748px;height:798px;background:var(--white)}
.hero{left:146px;top:145px;width:593px;height:242px;border-radius:3px;background:linear-gradient(100deg,#1f2a33 0%,#5a6a72 35%,#7b8a5a 60%,#3a3f2e 100%)}
.hero h1{position:absolute;left:282px;top:64px;width:300px;font-family:"Signika",sans-serif;font-weight:700;font-size:30px;line-height:30px;color:#fff}
.hero .read-more{position:absolute;left:283px;top:133px;background:var(--brand-red);color:#fff;font-family:"Signika",sans-serif;font-weight:600;font-size:13px;padding:6px 6px;border-radius:3px}

.categories-bar{left:146px;top:395px;width:593px;height:34px;background:linear-gradient(#3f76aa,#1e4f80);color:#fff;font-family:"Signika",sans-serif;font-weight:600;font-size:19px;padding:4px 12px}
.categories-grid{left:146px;top:429px;width:593px;height:355px;background:var(--panel-grey)}
.card{position:absolute;width:284px}
.card .photo{height:101px;border:1px solid #ccc;border-radius:2px}
.card .caption{margin-top:3px;height:37px;background:var(--brand-red);color:#fff;font-size:10.5px;line-height:13px;padding:5px 9px;font-weight:500}
.card .view-all{margin-top:6px;margin-left:2px;font-size:11px;font-weight:600;color:var(--link-blue)}

.tag-row{left:146px;width:593px;height:33px;background:var(--tag-blue);border:1px solid #2c5c88;color:#fff;font-size:20px}
.tag-row span{position:absolute;top:3px;transform:translateX(-50%)}

.ad-software{left:748px;top:145px;width:128px;height:482px;background:linear-gradient(#a8201c 0%,#c9c9c9 30%,#d9d9d9 55%,#9c1c18 75%,#7a1410 100%);text-align:center;color:#fff;font-family:"Signika",sans-serif}
.ad-software .brand{margin-top:14px;font-weight:700;font-size:17px}
.ad-software .pitch{margin-top:12px;font-weight:600;font-size:15px;line-height:15px}
.ad-software .box{width:86px;height:126px;margin:34px auto 0;background:linear-gradient(135deg,#222,#6a1a12 60%,#e2a23a)}
.ad-software ul{list-style:none;text-align:left;margin:54px 0 0 22px;font-size:12px;line-height:17px}
.ad-software ul li:before{content:"✓ ";color:#e8a0a0}
.ad-software .download{margin:12px auto 0;width:90px;background:#1a1a1a;border-radius:5px;font-weight:700;font-size:14px;line-height:14px;padding:5px 0}

.ad-psa{left:748px;top:638px;width:128px;height:288px;border:1px solid #ddd}
.ad-psa .art{height:173px;background:linear-gradient(#ffffff,#e7e0d4 60%,#c7b28f)}
.ad-psa .band{height:114px;background:#ef6a1f;color:#fff;font-family:"Signika",sans-serif;font-weight:700;padding:26px 0 0 7px}
.ad-psa .band .phone{font-size:14px;line-height:14px}
.ad-psa .band .web{font-size:12px}
.ad-psa .marks{display:flex;gap:8px;margin-top:16px}
.ad-psa .marks i{display:block;width:22px;height:22px;border-radius:50%;background:rgba(255,255,255,.75)}

.site-footer{left:80px;top:947px;width:805px;height:243px;background:var(--footer)}
.footer-col{position:absolute;top:28px}
.footer-col h3{font-weight:500;font-size:12.5px;color:var(--footer-text)}
.footer-col ul{list-style:none;margin-top:16px}
.footer-col li{font-size:9px;line-height:17px;color:var(--footer-link);text-decoration:underline}
.social-squares{position:absolute;left:578px;top:57px;display:flex;gap:10px}
.social-squares i{display:block;width:26px;height:26px;border-radius:2px}
.newsletter-title{position:absolute;left:578px;top:108px;font-size:12.5px;color:var(--footer-text)}
.newsletter{position:absolute;left:578px;top:127px;width:213px;height:25px;background:#2a2a2a;border:1px solid #3d3d3d;font-size:8.5px;font-style:italic;color:#777;padding:7px 10px}
.subscribe{position:absolute;left:723px;top:129px;width:66px;height:21px;background:var(--brand-red);color:#fff;font-size:10px;font-weight:500;text-align:center;line-height:21px}
.footer-rule{position:absolute;left:16px;top:197px;width:773px;height:1px;background:#4a4a4a}
.copyright{position:absolute;left:16px;top:213px;font-size:9.5px;color:#a8a8a8}
</style>
</head>
<body>

<header class="abs site-header">
  <div class="abs logo"><span class="logo-dot"></span><span class="logo-name">LUMRA LEARNING</span></div>
  <div class="abs search">Please enter your search</div>
  <div class="abs search-btn">
    <svg width="14" height="14" viewBox="0 0 14 14"><circle cx="6" cy="6" r="4.2" fill="none" stroke="#fff" stroke-width="2"/><line x1="9" y1="9" x2="13" y2="13" stroke="#fff" stroke-width="2.2"/></svg>
  </div>
</header>

<nav class="abs main-nav">
  <a class="active" style="width:142px">Home</a>
  <a style="width:143px">About Us</a>
  <a style="width:142px">Service</a>
  <a style="width:143px">New &amp; Event</a>
  <a style="width:133px">Blog</a>
  <a style="width:152px">Lumra Learning</a>
  <a style="width:149px;border-right:0">Contact Us</a>
</nav>

<aside class="abs side-menu">
  <div class="tile"><svg width="32" height="30" viewBox="0 0 32 30" fill="none" stroke="#fff" stroke-width="2"><path d="M3 14L15 3l12 11"/><path d="M6 12v14h9"/><ellipse cx="22" cy="21" rx="8" ry="5"/><circle cx="22" cy="21" r="2" fill="#fff"/></svg></div>
  <div class="tile"><svg width="32" height="28" viewBox="0 0 32 28" fill="#fff"><ellipse cx="12" cy="14" rx="10" ry="7"/><path d="M5 19l-2 7 7-4z"/><ellipse cx="21" cy="9" rx="9" ry="6" fill="none" stroke="#fff" stroke-width="2"/></svg></div>
  <div class="tile"><svg width="30" height="30" viewBox="0 0 30 30" stroke="#fff" stroke-width="3" fill="none"><path d="M5 25L25 5"/><path d="M5 5l20 20"/><circle cx="6" cy="6" r="3" fill="#fff"/></svg></div>
  <div class="tile"><svg width="24" height="30" viewBox="0 0 24 30" fill="none" stroke="#fff" stroke-width="2"><path d="M2 2h14l6 6v20H2z"/><path d="M6 14h12M6 18h12M6 22h12"/></svg></div>
  <div class="tile"><svg width="32" height="28" viewBox="0 0 32 28" fill="none" stroke="#fff" stroke-width="2"><rect x="2" y="2" width="28" height="24"/><path d="M2 8h28"/><rect x="6" y="12" width="10" height="10" fill="#fff"/><path d="M19 13h8M19 17h8M19 21h8"/></svg></div>
  <div class="tile"><svg width="30" height="30" viewBox="0 0 30 30" fill="none" stroke="#fff" stroke-width="2"><rect x="3" y="3" width="24" height="14"/><path d="M15 17v6M8 28l7-5 7 5"/><path d="M7 8h8M7 12h8"/></svg></div>
  <div class="tile"><svg width="28" height="28" viewBox="0 0 28 28" fill="#fff"><path d="M6 3l5 6-3 3c2 4 4 6 8 8l3-3 6 5-3 4C12 26 2 16 2 6z"/></svg></div>
</aside>

<div class="abs social-rail"><span></span><span></span><span></span><span></span><span></span><span></span><span></span></div>

<main class="abs content"></main>

<section class="abs hero" role="img" aria-label="Photo of a smiling student carrying a backpack outdoors">
  <h1>Contrairement à unei nion répandue</h1>
  <span class="read-more">Read More</span>
</section>

<div class="abs categories-bar">Categories</div>
<section class="abs categories-grid">
  <div class="card" style="left:8px;top:9px">
    <div class="photo" role="img" aria-label="Photo of a group of smiling students" style="background:linear-gradient(90deg,#3a2a22,#8a7464,#d9c7b0)"></div>
    <div class="caption">Plusieurs variations de Lorem Ipsumpeuve nt être trouvées ici ou.</div>
    <div class="view-all">View All »</div>
  </div>
  <div class="card" style="left:301px;top:9px">
    <div class="photo" role="img" aria-label="Photo of a student resting her chin on her hand at a desk" style="background:linear-gradient(90deg,#8d8f93,#c9c2b8,#e3e6e0)"></div>
    <div class="caption">Plusieurs variations de Lorem Ipsumpeuve nt être trouvées ici ou.</div>
    <div class="view-all">View All »</div>
  </div>
  <div class="card" style="left:8px;top:186px">
    <div class="photo" role="img" aria-label="Photo of a student working on a laptop" style="background:linear-gradient(90deg,#4a4a4a,#6e6e6e,#9a9a9a)"></div>
    <div class="caption">Plusieurs variations de Lorem Ipsumpeuve nt être trouvées ici ou.</div>
    <div class="view-all">View All »</div>
  </div>
  <div class="card" style="left:301px;top:186px">
    <div class="photo" role="img" aria-label="Photo of a graduate in a cap smiling" style="background:linear-gradient(90deg,#2a2420,#a07c62,#6c6a5e)"></div>
    <div class="caption">Plusieurs variations de Lorem Ipsumpeuve nt être trouvées ici ou.</div>
    <div class="view-all">View All »</div>
  </div>
</section>

<div class="abs tag-row" style="top:788px"><span style="left:230px">Europe</span><span style="left:383px">Drama</span></div>
<div class="abs tag-row" style="top:823px"><span style="left:230px">Asia</span><span style="left:383px">Science</span></div>
<div class="abs tag-row" style="top:859px"><span style="left:230px">Usa</span><span style="left:383px">English</span></div>
<div class="abs tag-row" style="top:894px"><span style="left:230px">France</span><span style="left:383px">Franch</span></div>

<aside class="abs ad-software">
  <div class="brand">SiteForge 5</div>
  <div class="pitch">Create<br>your website<br>in just<br>5 steps</div>
  <div class="box" role="img" aria-label="Software product box"></div>
  <ul><li>1400 Templates</li><li>Webshop</li><li>RSS feed</li><li>Member Areas</li><li>Blog</li></ul>
  <div class="download">DOWNLOAD<br>IT NOW!</div>
</aside>

<aside class="abs ad-psa">
  <div class="art" role="img" aria-label="Illustration of cartoon family characters"></div>
  <div class="band">
    <div class="phone">877-555-0142</div>
    <div class="web">Parentline.org</div>
    <div class="marks"><i></i><i></i><i></i><i></i></div>
  </div>
</aside>

<footer class="abs site-footer">
  <div class="footer-col" style="left:16px"><h3>Company</h3><ul><li>Contrairement</li><li>Opinion répandue</li><li>Pas simplement du</li><li>Texte aléatoire</li></ul></div>
  <div class="footer-col" style="left:156px"><h3>Dictionnaire de</h3><ul><li>Plusieurs variations</li><li>De Lorem Ipsum</li><li>Vent être</li></ul></div>
  <div class="footer-col" style="left:303px"><h3>Trouvées ici ou</h3><ul><li>Siècle est reproduit</li><li>Dessous pour les</li><li>CurieuxPlusieurs varia-</li><li>tions</li><li>De Lorem Ipsum</li></ul></div>
  <div class="footer-col" style="left:446px"><h3>Embarassantes</h3><ul><li>L'extrait standard</li><li>Utilisé depuis</li><li>Siècle est reproduit</li><li>Dessous pour les</li><li>Curieux</li><li>Vous voulez utiliser</li><li>Passage du Lorem</li></ul></div>
  <div class="footer-col" style="left:578px"><h3>Stay updates on our Socail Network</h3></div>
  <div class="social-squares"><i style="background:#3b6fb6"></i><i style="background:#4aa8e0"></i><i style="background:#1b82a8"></i></div>
  <div class="newsletter-title">Join Our Newsletter</div>
  <div class="newsletter">Enter your email address</div>
  <div class="subscribe">Subscribe</div>
  <div class="footer-rule"></div>
  <div class="copyright">© Copyrights 2013 All rights Reserved</div>
</footer>

</body>
</html>
```